KDWB Business Card

Looking for a business card design to incorporate our branding. We want to only use the colors listing in the Branding Package (attached).
Updates

Target Market(s)

People who need their phone or device fixed.

Industry/Entity Type

Electronics

Contact Information for Business Card

Please use:

Brightwick Gadget Clinic LLC
4810 E Harlow Ridge Rd
Suite 417
San Antonio, TX 78163

Marcus Delgrove, Store Manager

(210) 555-0147

Requirements
Must have
• Must include the colors that are contained within the Branding Package PDF file.

```html
<!DOCTYPE html>
<html lang="en">
<head>
<meta charset="utf-8">
<title>Brightwick Gadget Clinic – Business Card</title>
<link rel="stylesheet" href="https://fonts.googleapis.com/css2?family=Arimo:wght@400&display=swap">
<style>
  :root {
    --brand-orange: #f05325;
    --card-white: #ffffff;
    --text-dark: #3d3d3d;
    --text-grey: #6b6b6b;
    --stage: #5b5b5b;
  }
  * { box-sizing: border-box; margin: 0; padding: 0; }
  html, body {
    width: 1200px;
    height: 1082px;
    overflow: hidden;
  }
  body {
    position: relative;
    background: var(--stage);
    font-family: "Arimo", Arial, sans-serif;
  }
  .card {
    position: absolute;
    width: 629px;
    height: 356px;
    box-shadow: 0 3px 8px rgba(0, 0, 0, 0.45);
  }
  .card--front {
    left: 286px;
    top: 180px;
    background: radial-gradient(ellipse at 70% 35%, var(--card-white) 40%, #f1f1f1 100%);
  }
  .card--back {
    left: 289px;
    top: 569px;
    background: var(--brand-orange);
  }
  .brand {
    position: absolute;
    display: flex;
    align-items: center;
    gap: 12px;
    font-size: 27px;
    line-height: 1;
    white-space: nowrap;
  }
  .brand__mark {
    width: 52px;
    height: 52px;
    border-radius: 8px;
    flex: none;
  }
  .card--front .brand {
    left: 38px;
    top: 54px;
    color: var(--brand-orange);
  }
  .card--front .brand__mark { background: var(--brand-orange); }
  .card--back .brand {
    left: 50%;
    top: 50%;
    transform: translate(-50%, -50%);
    color: var(--card-white);
  }
  .card--back .brand__mark { background: var(--card-white); }
  .contact {
    position: absolute;
    left: 36px;
    top: 255px;
    line-height: 1;
  }
  .contact__name {
    font-size: 23px;
    color: var(--brand-orange);
    margin-bottom: 10px;
  }
  .contact__title {
    font-size: 17px;
    color: var(--text-grey);
    margin-bottom: 9px;
  }
  .contact__phone {
    font-size: 16px;
    color: var(--text-dark);
  }
  .contact__label { color: var(--brand-orange); }
  .address {
    position: absolute;
    left: 323px;
    top: 259px;
    font-style: normal;
    font-size: 15.5px;
    line-height: 25px;
    color: var(--text-dark);
  }
</style>
</head>
<body>
  <section class="card card--front" aria-label="Business card front">
    <div class="brand">
      <span class="brand__mark"></span>
      <span class="brand__name">Brightwick Gadget Clinic</span>
    </div>
    <div class="contact">
      <p class="contact__name">Marcus Delgrove</p>
      <p class="contact__title">Store Manager</p>
      <p class="contact__phone"><span class="contact__label">Phone:</span> (210) 555-0147</p>
    </div>
    <address class="address">
      4810 E Harlow Ridge Rd<br>
      Suite 417<br>
      San Antonio, TX 78163
    </address>
  </section>

  <section class="card card--back" aria-label="Business card back">
    <div class="brand">
      <span class="brand__mark"></span>
      <span class="brand__name">Brightwick Gadget Clinic</span>
    </div>
  </section>
</body>
</html>
```